VeraMosk Powerpoint design

We've recently redesigned our logos and would like a single presentation format that we can easily interchange the logos attached into. The presentation will be used for general company sales information. The group is called VeraMosk and has 2 companies, k7datagrove and Copper Thread. We're an IT services company who specialises in Broadband and general network services.

Target Market(s)

Professional

```html
<!DOCTYPE html>
<html lang="en">
<head>
<meta charset="utf-8">
<title>VeraMosk Group – Company Presentation</title>
<link rel="stylesheet" href="https://fonts.googleapis.com/css2?family=Saira:wght@500;600;700;800&family=Open+Sans:ital,wght@0,400;0,600;1,400&display=swap">
<style>
:root{
  --page:#4a4a4a;
  --blue:#2a9fd8;
  --blue-deep:#1676b0;
  --ink:#111418;
  --body:#4b5058;
  --muted:#8a9098;
  --white:#ffffff;
  --paper:#f7f8fa;
  --green:#2e9a56;
  --dark:#141c24;
}
*{box-sizing:border-box;margin:0;padding:0}
html,body{width:1200px;height:4149px;overflow:hidden;background:var(--page)}
body{position:relative;font-family:"Open Sans",Arial,sans-serif;color:var(--body)}
.slide{position:absolute;left:50px;width:1098px;height:617px;overflow:hidden;background:var(--paper)}
.abs{position:absolute}
.head{font-family:"Saira",Arial,sans-serif;font-weight:700;color:var(--ink);letter-spacing:.5px;text-transform:uppercase}
.eyebrow{font-family:"Saira",Arial,sans-serif;font-weight:600;color:var(--blue);text-transform:uppercase;font-size:14px;letter-spacing:.4px}
.copy{font-size:12px;line-height:23px;color:var(--body)}
.brand{position:absolute;display:flex;align-items:center;gap:8px;font-family:"Saira",Arial,sans-serif;font-weight:600;color:var(--ink)}
.brand .dot{width:22px;height:22px;border-radius:50%;background:var(--green);flex:none}
.brand-main{font-size:34px;line-height:1}
.brand-main .sub{display:block;font-size:12px;letter-spacing:3px;text-align:right;margin-top:-2px}
.brand-main .dot{width:30px;height:30px}
.footer-brands .brand{font-size:22px;top:560px}
.photo{position:absolute}

/* slide 1 */
.hero{top:64px;background:linear-gradient(120deg,#1f8fcf 0%,#3aa8e0 45%,#5fb7e2 70%,#1a6e9e 100%)}
.hero .tag{left:84px;top:119px;height:39px;padding:0 12px;background:var(--white);color:var(--blue);font-family:"Saira",Arial,sans-serif;font-weight:700;font-size:28px;line-height:39px}
.hero .title{left:84px;top:170px;color:var(--white);font-size:92px;line-height:96px;font-weight:800}
.hero .lead{left:89px;top:386px;width:430px;color:var(--white);font-size:13.5px;line-height:26px}

/* slide 2 */
.about{top:738px}
.about .bullets{left:560px;top:428px;list-style:none;font-size:12px;line-height:23px;color:var(--ink)}
.about .bullets li{display:flex;align-items:center;gap:9px}
.about .bullets li::before{content:"";width:7px;height:7px;border:2px solid var(--green);border-radius:50%}

/* slide 6 */
.closing{top:3469px;background:var(--white)}
.closing .panel{left:660px;top:0;width:438px;height:277px;background:var(--blue)}
.contact{left:714px;list-style:none;font-size:16px;line-height:24px;color:var(--ink)}
.contact li{position:absolute;left:0;display:flex;gap:14px;width:340px}
.contact svg{flex:none;margin-top:3px}
</style>
</head>
<body>

<!-- Slide 1: Welcome -->
<section class="slide hero">
  <div class="photo" role="img" aria-label="Smiling IT professional holding a laptop in a blue-lit server room" style="left:560px;top:0;width:538px;height:617px;background:linear-gradient(90deg,rgba(255,255,255,0) 0%,rgba(220,236,246,.35) 50%,rgba(20,70,110,.35) 100%)"></div>
  <div class="abs tag">WELCOME TO</div>
  <h1 class="abs head title">VERAMOSK<br>GROUP</h1>
  <p class="abs lead">Lorem ipsum dolor sit amet, consectetur adipiscing elit, sed do eiusmod tempor incididunt ut labore et dolore magna aliqua. Quis ipsum suspendisse ultrices gravida. Risus commodo viverra maecenas accumsan lacus vel facilisis.</p>
</section>

<!-- Slide 2: About us -->
<section class="slide about">
  <svg class="abs" style="left:0;top:0" width="1098" height="617" viewBox="31 458 682 383" role="img" aria-label="Office and support desk photographs set in rounded vertical strips">
    <defs><linearGradient id="strip" x1="0" y1="0" x2="0" y2="1"><stop offset="0" stop-color="#c9d0d6"/><stop offset="1" stop-color="#6f7a84"/></linearGradient></defs>
    <g fill="url(#strip)">
      <rect x="31" y="400" width="47" height="255" rx="23.5"/>
      <rect x="83" y="400" width="57" height="378" rx="28.5"/>
      <rect x="146" y="400" width="56" height="322" rx="28"/>
      <rect x="208" y="400" width="58" height="286" rx="29"/>
      <rect x="272" y="400" width="62" height="243" rx="31"/>
      <rect x="336" y="400" width="56" height="207" rx="28"/>
      <rect x="398" y="400" width="58" height="165" rx="29" fill="#3d4650"/>
      <rect x="462" y="400" width="57" height="140" rx="28.5" fill="#4c5660"/>
    </g>
  </svg>
  <div class="brand brand-main" style="left:888px;top:24px"><span class="dot"></span><span>VeraMosk<span class="sub">GROUP</span></span></div>
  <p class="abs eyebrow" style="left:560px;top:274px;font-size:12px">About us</p>
  <h2 class="abs head" style="left:560px;top:302px;font-size:38px">VeraMosk Group</h2>
  <p class="abs" style="left:560px;top:367px;width:470px;font-size:13px;line-height:22px;font-style:italic;color:var(--blue)">Lorem ipsum dolor sit amet, consectetur adipiscing elit, sed do eiusmod tempor incididunt ut labore et dolore magna aliqua.</p>
  <ul class="abs bullets">
    <li>Lorem Ipsum is simply dummy text of the printing</li>
    <li>Lorem Ipsum is simply dummy text of the</li>
    <li>Lorem Ipsum is simply dummy text of</li>
    <li>Lorem Ipsum is simply dummy text of</li>
  </ul>
  <div class="footer-brands">
    <div class="brand" style="left:664px"><span class="dot"></span>Copper Thread</div>
    <div class="brand" style="left:852px"><span class="dot"></span>k7datagrove</div>
  </div>
</section>

<!-- Slide 3: What we do -->
<section class="slide" style="top:1418px">
  <p class="abs eyebrow" style="left:58px;top:98px">What we do</p>
  <h2 class="abs head" style="left:58px;top:130px;font-size:42px;letter-spacing:2px">Lorem Ipsum</h2>
  <div class="abs copy" style="left:58px;top:205px;width:490px">
    <p>Lorem ipsum dolor sit amet, consectetur adipiscing elit, sed do eiusmod tempor incididunt ut labore et dolore magna aliqua. Quis ipsum suspendisse ultrices gravida. Risus commodo viverra maecenas accumsan lacus vel facilisis.</p>
    <p style="margin-top:23px">Lorem ipsum dolor sit amet, consectetur adipiscing elit, sed do eiusmod tempor incididunt ut labore et dolore magna aliqua. Quis ipsum suspendisse ultrices gravida. Risus commodo viverra maecenas accumsan lacus vel facilisis.</p>
    <p style="margin-top:23px">Lorem ipsum dolor sit amet, consectetur adipiscing elit, sed do eiusmod tempor incididunt ut labore et dolore magna aliqua. Quis ipsum suspendisse ultrices gravida. Risus commodo viverra maecenas accumsan lacus vel facilisis.</p>
    <p style="margin-top:23px">Lorem ipsum dolor sit amet, consectetur adipiscing elit, sed do eiusmod tempor incididunt ut labore et dolore magna aliqua. Quis ipsum suspendisse ultrices gravida. Risus</p>
  </div>
  <div class="photo" role="img" aria-label="Server racks with blue lights in a data centre" style="left:577px;top:0;width:452px;height:524px;border-radius:0 0 10px 64px;background:linear-gradient(135deg,#243646 0%,#0f1c27 45%,#4a6478 100%)"></div>
  <div class="brand brand-main" style="left:888px;top:24px;color:var(--white)"><span class="dot"></span><span>VeraMosk<span class="sub">GROUP</span></span></div>
  <div class="footer-brands">
    <div class="brand" style="left:664px"><span class="dot"></span>Copper Thread</div>
    <div class="brand" style="left:852px"><span class="dot"></span>k7datagrove</div>
  </div>
</section>

<!-- Slide 4: Services -->
<section class="slide" style="top:2106px">
  <div class="brand brand-main" style="left:888px;top:24px"><span class="dot"></span><span>VeraMosk<span class="sub">GROUP</span></span></div>
  <div class="photo" role="img" aria-label="Data centre aisle between server racks" style="left:18px;top:90px;width:193px;height:296px;border-radius:6px;background:linear-gradient(180deg,#1c3244,#0b1620)"></div>
  <div class="photo" role="img" aria-label="Technician working on a laptop beside servers" style="left:232px;top:90px;width:193px;height:296px;border-radius:6px;background:linear-gradient(180deg,#3a4b5a,#1a2530)"></div>
  <div class="photo" role="img" aria-label="Colleague working at a desktop computer in a bright office" style="left:445px;top:90px;width:193px;height:296px;border-radius:6px;background:linear-gradient(180deg,#d9d6d0,#8a6a5a)"></div>
  <div class="abs" style="left:18px;top:393px;width:193px;height:104px;background:var(--white);border-radius:6px;box-shadow:0 2px 8px rgba(0,0,0,.1);text-align:center;padding-top:14px">
    <p class="head" style="font-size:16px">Lorem Ipsum</p>
    <p style="font-size:9px;line-height:16px;color:var(--muted);padding:4px 10px 0">Lorem ipsum dolor sit amet, consectetur adipiscing elit, sed do eiusmod tempor incididunt ut</p>
  </div>
  <div class="abs" style="left:223px;top:397px;width:211px;height:145px;background:var(--blue);border-radius:6px;text-align:center;padding-top:26px">
    <p class="head" style="font-size:17px;color:var(--white)">Lorem Ipsum</p>
    <p style="font-size:10px;line-height:18px;color:var(--white);padding:6px 14px 0">Lorem ipsum dolor sit amet, consectetur adipiscing elit, sed do eiusmod tempor incididunt ut</p>
  </div>
  <div class="abs" style="left:445px;top:393px;width:193px;height:136px;background:var(--white);border-radius:6px;box-shadow:0 2px 8px rgba(0,0,0,.1);text-align:center;padding-top:22px">
    <p class="head" style="font-size:16px">Lorem Ipsum</p>
    <p style="font-size:9px;line-height:18px;color:var(--muted);padding:6px 16px 0">Lorem ipsum dolor sit amet, consectetur adipiscing elit, sed do eiusmod tempor incididunt</p>
  </div>
  <p class="abs eyebrow" style="left:686px;top:156px;font-size:17px">Our services</p>
  <h2 class="abs head" style="left:686px;top:182px;font-size:38px;line-height:46px">VeraMosk Group<br>Services</h2>
  <div class="abs copy" style="left:686px;top:290px;width:370px;color:var(--muted)">
    <p>Lorem ipsum dolor sit amet, consectetur adipiscing elit, sed do eiusmod tempor incididunt ut labore et dolore magna aliqua. Quis ipsum suspendisse ultrices gravida. Risus commodo viverra maecenas accumsan lacus vel facilisis.</p>
    <p style="margin-top:23px">Lorem ipsum dolor sit amet, consectetur adipiscing elit, sed do eiusmod tempor incididunt ut labore et dolore magna aliqua. Quis ipsum suspendisse ultrices gravida.</p>
  </div>
  <div class="footer-brands">
    <div class="brand" style="left:664px"><span class="dot"></span>Copper Thread</div>
    <div class="brand" style="left:852px"><span class="dot"></span>k7datagrove</div>
  </div>
</section>

<!-- Slide 5: Why choose us -->
<section class="slide" style="top:2790px">
  <div class="photo" role="img" aria-label="Engineers discussing in a dark server room" style="left:0;top:0;width:1098px;height:396px;background:linear-gradient(90deg,#1a2128 0%,#2e3a44 50%,#1c242c 100%)"></div>
  <div class="brand brand-main" style="left:888px;top:24px;color:var(--white)"><span class="dot"></span><span>VeraMosk<span class="sub">GROUP</span></span></div>
  <p class="abs head" style="left:0;width:1098px;top:70px;text-align:center;color:var(--white);font-size:18px">Lorem Ipsum</p>
  <h2 class="abs head" style="left:0;width:1098px;top:104px;text-align:center;color:var(--white);font-size:38px">Why choose us?</h2>
  <p class="abs" style="left:261px;top:164px;width:580px;text-align:center;color:var(--white);font-size:12px;line-height:23px">Lorem ipsum dolor sit amet, consectetur adipiscing elit, sed do eiusmod tempor incididunt ut labore et dolore magna aliqua. Quis ipsum suspendisse ultrices gravida. Risus commodo viverra maecenas accumsan lacus vel facilisis.</p>
  <p class="abs head" style="left:0;width:1098px;top:274px;text-align:center;color:var(--white);font-size:18px">Our clients</p>
  <div class="abs" style="left:251px;top:331px;width:563px;height:70px;background:var(--paper)"></div>
  <div class="abs head" style="left:265px;top:362px;width:536px;display:grid;grid-template-columns:repeat(4,1fr);row-gap:52px;text-align:center;font-size:20px;color:#3c4652">
    <span>Kestrel</span><span>Tornvale</span><span>Brightmoor</span><span>Elvanor</span>
    <span>Harlow</span><span>Novique</span><span>Delmar</span><span>Ostrin</span>
  </div>
  <div class="footer-brands">
    <div class="brand" style="left:664px"><span class="dot"></span>Copper Thread</div>
    <div class="brand" style="left:852px"><span class="dot"></span>k7datagrove</div>
  </div>
</section>

<!-- Slide 6: Thank you -->
<section class="slide closing">
  <div class="photo" role="img" aria-label="Person walking through a server corridor toward a cloud" style="left:0;top:0;width:660px;height:617px;background:radial-gradient(ellipse at 50% 45%,#b8c0c6 0%,#5a6670 35%,#141c24 75%)"></div>
  <div class="abs panel"></div>
  <div class="brand" style="left:714px;top:30px;font-size:54px;color:var(--white)"><span class="dot" style="width:40px;height:40px;background:var(--white)"></span><span>VeraMosk</span></div>
  <p class="abs" style="left:696px;top:122px;width:380px;color:var(--white);font-size:11.5px;line-height:20px">Lorem ipsum dolor sit amet, consectetur adipiscing elit, sed do eiusmod tempor incididunt ut labore et dolore magna aliqua. Quis ipsum suspendisse ultrices gravida. Risus commodo viverra maecenas accumsan lacus vel facilisis. Lorem ipsum dolor sit amet, consectetur adipiscing elit, sed do eiusmod</p>
  <h2 class="abs head" style="left:714px;top:312px;font-size:36px">Thank you</h2>
  <ul class="abs contact" style="top:0">
    <li style="top:386px"><svg width="16" height="18" viewBox="0 0 16 18"><path d="M8 0a6 6 0 0 0-6 6c0 4.5 6 12 6 12s6-7.5 6-12a6 6 0 0 0-6-6zm0 8.3A2.3 2.3 0 1 1 8 3.7a2.3 2.3 0 0 1 0 4.6z" fill="var(--blue)"/></svg><span>Lorem Ipsum is simply dummy<br>ext of the printing</span></li>
    <li style="top:458px"><svg width="16" height="16" viewBox="0 0 16 16"><path d="M3.3 0l3 3.6-1.7 2a10 10 0 0 0 5.8 5.8l2-1.7L16 12.7 14 16C6.3 15.7.3 9.7 0 2z" fill="var(--blue)"/></svg><span>+1 888 888 8888</span></li>
    <li style="top:503px"><svg width="16" height="16" viewBox="0 0 16 16" fill="none" stroke="var(--blue)" stroke-width="1.6"><circle cx="8" cy="8" r="7"/><ellipse cx="8" cy="8" rx="3" ry="7"/><path d="M1 8h14"/></svg><span>https://www.veramosk.com</span></li>
    <li style="top:550px"><svg width="17" height="13" viewBox="0 0 17 13"><rect width="17" height="13" rx="1.5" fill="var(--blue)"/><path d="M1 1.5l7.5 6 7.5-6" stroke="#fff" stroke-width="1.4" fill="none"/></svg><span>hello@veramosk.com</span></li>
  </ul>
</section>

</body>
</html>
```